Private practice for psychiatry and psychotherapy needs a business card and logo

I need a logo and business card design for my private practice for psychiatry and psychotherapy. The optional names for my practice are: Vorsteling Praktijk voor Psychiatrie en Psychotherapie, or short: Praktijk Vorsteling.
I am a (child and adolescent) psychiatrist and psychotherapist. I diagnose and treat infants, children, adolescents and adults with psychiatric symptoms/disorders. I also give supervision to colleagues about their own treatments. My work is characterised by personal involvement, transparence, creativity and professionality.
I would like to have an appealing, light and bright, yet basic design that invites people (both children and adults) to contact me, gives trust and hope, without loosing professional appearance.
I uploaded my contact information which should not necessarily be all included (in this form) on the card as long as people know how to contact me. Please feel free to be creative!
Please note that my website is only temporarely and need a new design and update too!

Target Market(s)

Clients and patients (children, adolescents, adults) with psychiatric symptoms who need diagnosis and treatment. I work with private clients and patients through medical insurances.

Industry/Entity Type

Mental Health

Contact Information for Business Card

Dr. Ilse Vorsteling-ter Haaf
Psychiater/Kinder- en Jeugdpsychiater
Jorisvan Heultstraat 14
3071 PW Rotterdam
t: 06-58190274
e: info@praktijkvorsteling.nl
i: www.praktijkvorsteling.nl

Logo Text

Praktijk Vorsteling voor Psychiatrie en Psychotherapie; or short: Praktijk Vorsteling

Font styles to use
Sans Serif
Other font styles liked:
• up to designer

Requirements
Must have
• Appealing, light, bright, creative, trustful, professional and unique.

```html
<!DOCTYPE html>
<html lang="nl">
<head>
<meta charset="utf-8">
<title>Praktijk Vorsteling – visitekaartje</title>
<link rel="stylesheet" href="https://fonts.googleapis.com/css2?family=Open+Sans:wght@400;600&family=Roboto+Condensed:wght@400;700&display=swap">
<style>
  :root {
    --page-bg: #e9edf0;
    --teal: #5ec4c8;
    --sky: #44a5dc;
    --blue: #3d9fd8;
    --blue-light: #7cc4ea;
    --ink: #3a3a3a;
    --muted: #6b6b6b;
    --white: #ffffff;
  }
  * { box-sizing: border-box; margin: 0; padding: 0; }
  html, body { width: 1200px; height: 1000px; overflow: hidden; }
  body {
    background: var(--page-bg);
    font-family: "Open Sans", Arial, sans-serif;
    position: relative;
  }
  .card {
    position: absolute;
    left: 290px;
    width: 620px;
    height: 360px;
    border-radius: 26px;
    overflow: hidden;
    box-shadow: 0 14px 34px rgba(0, 0, 0, 0.14);
  }
  /* front side */
  .card--front {
    top: 100px;
    background: linear-gradient(30deg, var(--teal) 0%, #56b8d4 50%, var(--sky) 100%);
    display: flex;
    flex-direction: column;
    align-items: center;
    justify-content: center;
    gap: 18px;
  }
  .brand-dot {
    width: 54px; height: 54px;
    border: 2px solid var(--white);
    border-radius: 50%;
  }
  .brand-name {
    font-family: "Open Sans", Arial, sans-serif;
    font-weight: 400;
    color: var(--white);
    font-size: 21px;
    letter-spacing: 1px;
  }
  /* back side */
  .card--back {
    top: 540px;
    background: var(--white);
  }
  .back-band { position: absolute; inset: 0; }
  .edge-tab {
    position: absolute;
    left: 0; top: 114px;
    width: 6px; height: 42px;
    background: var(--blue);
  }
  .back-brand {
    position: absolute;
    right: 40px; top: 56px;
    width: 150px;
    display: flex; flex-direction: column; align-items: center; gap: 12px;
  }
  .back-brand .brand-dot { width: 44px; height: 44px; border-color: var(--blue); }
  .back-brand .brand-name { color: var(--ink); font-size: 13px; letter-spacing: 0.4px; white-space: nowrap; }
  .person {
    position: absolute;
    left: 50px; top: 104px;
  }
  .person-name {
    font-family: "Roboto Condensed", "Arial Narrow", sans-serif;
    font-weight: 700;
    font-size: 26px;
    color: var(--ink);
    text-transform: uppercase;
    letter-spacing: 0.2px;
  }
  .person-role {
    font-family: "Roboto Condensed", "Arial Narrow", sans-serif;
    font-weight: 400;
    font-size: 17px;
    color: var(--blue);
    margin-top: 2px;
  }
  .contact {
    position: absolute;
    left: 50px; top: 184px;
    list-style: none;
    font-size: 13px;
    color: var(--muted);
    line-height: 18px;
  }
  .contact li { display: flex; align-items: flex-start; gap: 10px; }
  .contact li + li { margin-top: 2px; }
  .contact .address { margin-bottom: 6px; }
  .contact svg { width: 12px; height: 12px; margin-top: 3px; flex: none; fill: var(--blue); }
  .web-domain { color: var(--blue); }
</style>
</head>
<body>

<section class="card card--front" aria-label="Voorkant visitekaartje">
  <span class="brand-dot" aria-hidden="true"></span>
  <p class="brand-name">PRAKTIJK VORSTELING</p>
</section>

<section class="card card--back" aria-label="Achterkant visitekaartje">
  <svg class="back-band" viewBox="0 0 620 360" preserveAspectRatio="none" aria-hidden="true">
    <polygon points="0,346 620,262 620,276 0,354" fill="var(--blue-light)"/>
    <polygon points="0,354 620,276 620,360 0,360" fill="var(--blue)"/>
  </svg>
  <span class="edge-tab" aria-hidden="true"></span>

  <div class="back-brand">
    <span class="brand-dot" aria-hidden="true"></span>
    <p class="brand-name">PRAKTIJK VORSTELING</p>
  </div>

  <div class="person">
    <h1 class="person-name">Dr. Ilse Vorsteling-ter Haaf</h1>
    <p class="person-role">Psychiater/Kinder- en Jeugdpsychiater</p>
  </div>

  <ul class="contact">
    <li class="address">
      <svg viewBox="0 0 12 12"><path d="M1 5 L11 1 L7 11 L6 6 Z"/></svg>
      <span>Jorisvan Heultstraat 14<br>3071 PW Rotterdam</span>
    </li>
    <li>
      <svg viewBox="0 0 12 12"><path d="M2.5 1 L4.5 1 L5.3 3.6 L4 4.6 C4.7 6 6 7.3 7.4 8 L8.4 6.7 L11 7.5 L11 9.5 C11 10.3 10.3 11 9.5 11 C5 11 1 7 1 2.5 C1 1.7 1.7 1 2.5 1 Z"/></svg>
      <span>06-58190274</span>
    </li>
    <li>
      <svg viewBox="0 0 12 12"><path d="M1 3 L11 3 L11 10 L1 10 Z M1.6 3.4 L6 7 L10.4 3.4" fill="var(--blue)" stroke="var(--white)" stroke-width="0.8"/></svg>
      <span>info@praktijkvorsteling.nl</span>
    </li>
    <li>
      <svg viewBox="0 0 12 12"><circle cx="7" cy="5" r="3.5" fill="none" stroke="var(--blue)" stroke-width="1.5"/><path d="M4.6 7.4 L1.5 10.5" stroke="var(--blue)" stroke-width="1.6"/></svg>
      <span>www.<span class="web-domain">praktijkvorsteling</span>.nl</span>
    </li>
  </ul>
</section>

</body>
</html>
```